Banner Ad Design Project: Velvet Nook Club

VelvetNookClub.com is a community/personals website for those who enjoy the Sissy Maid Fetish.

Our membership typically falls into 3 categories:
1) Dominant women, men and transgendered people,
2) Submissive women, men and transgender people, and
3) People who can be either dominant or submissive (switches).

The fetish itself can involve a dominant or dominants along with sissy maids.

VelvetNookClub.com is not a porn website but it is meant for adult members.

What I need are 2 sizes of advertising banners:
1) 468 x 60 banner
2) 160 x 600 banner

You can checkout my website at: http://velvetnookclub.com
Use the username: reviewer
and the password: reviewer

I've attached 4 files, but there's no requirement that you use any of them. Graphics done by yourselves is OK also.

Target Market(s)

The target market is men; Straight, Bi & Gay and women; Straight, Bi & Gay.

Industry/Entity Type

Advertising

Requirements
Must have
• It should have Join Now somewhere on the banner,
It should indicate that the website is; a community for those interested in the sissy maid fetish

```html
<!DOCTYPE html>
<html lang="en">
<head>
<meta charset="utf-8">
<title>Velvet Nook Club – Banner</title>
<link rel="stylesheet" href="https://fonts.googleapis.com/css2?family=Source+Sans+3:wght@400;600;700&display=swap">
<style>
  :root {
    --black: #000000;
    --white: #ffffff;
    --strip-red: #c21d2c;
    --pink-light: #ff6fd8;
    --pink-mid: #f23ec6;
    --pink-deep: #e0159e;
    --wall: #d9d9db;
    --wall-dark: #bdbdc0;
    --floor: #a8714a;
    --floor-dark: #7d4f31;
  }
  html, body {
    margin: 0;
    padding: 0;
    width: 1200px;
    height: 4505px;
    overflow: hidden;
    background: var(--black);
  }
  .banner {
    position: relative;
    width: 1200px;
    height: 4505px;
    font-family: "Source Sans 3", "Myriad Pro", sans-serif;
    color: var(--white);
    background: var(--black);
  }
  .site-bar {
    position: absolute;
    left: 0; top: 0;
    width: 1200px; height: 335px;
    background: var(--black);
  }
  .site-url {
    position: absolute;
    left: 0; right: 0; top: 30px;
    text-align: center;
    font-size: 76px;
    font-weight: 400;
    line-height: 1;
    letter-spacing: -0.5px;
  }
  .accent-strip {
    position: absolute;
    left: 0; top: 335px;
    width: 1200px; height: 40px;
    background: var(--strip-red);
  }
  .pitch-panel {
    position: absolute;
    left: 0; top: 375px;
    width: 1200px; height: 1434px;
    background: linear-gradient(180deg, var(--pink-light) 0%, var(--pink-mid) 45%, var(--pink-deep) 100%);
    text-align: center;
    font-weight: 700;
    text-shadow: 0 4px 8px rgba(90, 0, 60, 0.45);
  }
  .pitch-title {
    position: absolute;
    left: 0; right: 0; top: 222px;
    margin: 0;
    font-size: 122px;
    line-height: 1;
    font-weight: 700;
  }
  .pitch-lines {
    position: absolute;
    left: 0; right: 0; top: 385px;
    margin: 0;
    font-size: 106px;
    line-height: 125px;
    font-weight: 700;
  }
  .photo-area {
    position: absolute;
    left: 0; top: 1809px;
    width: 1200px; height: 1874px;
    background: linear-gradient(180deg, var(--wall) 0%, var(--wall-dark) 62%, var(--floor) 74%, var(--floor-dark) 100%);
  }
  .cta-area {
    position: absolute;
    left: 0; top: 3683px;
    width: 1200px; height: 822px;
    background: var(--black);
  }
  .tagline {
    position: absolute;
    left: 0; right: 0; top: 130px;
    margin: 0;
    text-align: center;
    font-size: 112px;
    font-weight: 400;
    line-height: 1;
  }
  .join-button {
    position: absolute;
    left: 72px; top: 397px;
    width: 1056px; height: 245px;
    box-sizing: border-box;
    border: 10px solid var(--white);
    border-radius: 125px;
    background: linear-gradient(180deg, var(--pink-light) 0%, var(--pink-mid) 50%, var(--pink-deep) 100%);
    display: flex;
    align-items: center;
    justify-content: center;
    font-size: 170px;
    font-weight: 700;
    line-height: 1;
    color: var(--white);
    text-decoration: none;
    text-shadow: 0 4px 8px rgba(90, 0, 60, 0.4);
  }
</style>
</head>
<body>
  <div class="banner">
    <header class="site-bar">
      <div class="site-url">www.VelvetNookClub.com</div>
    </header>
    <div class="accent-strip"></div>

    <section class="pitch-panel">
      <h1 class="pitch-title">Sissy Maid Fetish</h1>
      <p class="pitch-lines">for the pleasure of<br>Dommes, Masters,<br>sissies, maids and<br>sissy maids<br>everywhere.</p>
    </section>

    <div class="photo-area" role="img" aria-label="Photo of a man in a maid's apron sweeping a wooden floor with a broom, lifting the corner of a grey wall to reveal brick underneath"></div>

    <footer class="cta-area">
      <p class="tagline">The Best Community</p>
      <a class="join-button" href="http://velvetnookclub.com">JOIN NOW</a>
    </footer>
  </div>
</body>
</html>
```